Mailing Brochure

I need a cover for a brochure that we are doing here locally. The only thing I am worried about is the COVER. The size of the brochure is 8.5 x 11 in.
We have a reasonable design for the inserts and back cover. We will mail the packet to accident victims that may need a lawyer. I am including a copy of our current tri-fold brochure that this will replace. The copy from that brochure will be in the inserts. We want something a little similar to that brochure- emphasizing good results and happy people, with maybe a little more legal flavor. I have included photos Pilgrave and the firm's building.
Thanks for your help.

```html
<!DOCTYPE html>
<html lang="en">
<head>
<meta charset="utf-8">
<title>Pilgrave Law Group – Brochure Cover</title>
<link rel="stylesheet" href="https://fonts.googleapis.com/css2?family=EB+Garamond:wght@400&family=Montserrat:wght@300;400;600;800&display=swap">
<style>
  :root {
    --backdrop: #e9eaec;
    --paper: #ffffff;
    --brand-blue: #1a5a8c;
    --navy: #0f2f5e;
    --navy-deep: #0a2349;
    --steel: #3d3f44;
    --sky-light: #ecebe7;
    --sky-mid: #c9c4bb;
    --sand: #b89a78;
    --sea: #8c8f8f;
    --white: #ffffff;
  }
  * { box-sizing: border-box; margin: 0; padding: 0; }
  html, body { width: 1200px; height: 900px; overflow: hidden; background: var(--backdrop); }
  .canvas { position: relative; width: 1200px; height: 900px; }
  .cover {
    position: absolute; left: 267px; top: 20px;
    width: 666px; height: 860px;
    background: var(--paper);
    overflow: hidden;
    box-shadow: 0 6px 24px rgba(0,0,0,.18);
  }
  .masthead { position: absolute; left: 0; top: 0; width: 100%; height: 158px; }
  .brand {
    position: absolute; left: 186px; top: 48px;
    display: flex; align-items: center; gap: 14px;
  }
  .brand-mark { width: 58px; height: 58px; background: var(--brand-blue); }
  .brand-name {
    font-family: "EB Garamond", serif; font-weight: 400;
    color: var(--brand-blue); font-size: 30px; line-height: 1.05;
    letter-spacing: 2px; text-transform: uppercase;
  }
  .tagline {
    position: absolute; left: 0; right: 0; top: 118px; text-align: center;
    font-family: "EB Garamond", serif; font-size: 16px; color: var(--brand-blue);
  }
  .rule-top { position: absolute; left: 0; top: 156px; width: 100%; height: 3px; background: var(--brand-blue); }
  .photo {
    position: absolute; left: 0; top: 159px; width: 100%; height: 480px;
    background:
      linear-gradient(180deg, var(--sky-light) 0%, var(--sky-mid) 58%, var(--sea) 70%, var(--sand) 88%, #a78a69 100%);
  }
  .base { position: absolute; left: 0; top: 540px; width: 666px; height: 320px; }
  .headline {
    position: absolute; left: 48px; top: 690px;
    font-family: Montserrat, sans-serif; color: var(--white);
    font-size: 33px; line-height: 1.15; letter-spacing: .3px;
  }
  .headline .light { font-weight: 300; }
  .headline .strong { font-weight: 800; }
  .contact {
    position: absolute; right: 44px; top: 716px; text-align: right;
    font-family: Montserrat, sans-serif; color: var(--white);
  }
  .contact .phone { font-size: 25px; font-weight: 800; letter-spacing: 1px; }
  .contact .web { font-size: 13px; font-weight: 400; margin-top: 2px; }
  .rule-bottom { position: absolute; left: 48px; right: 44px; top: 800px; height: 1px; background: rgba(255,255,255,.28); }
  .address {
    position: absolute; left: 0; right: 0; top: 818px; text-align: center;
    font-family: Montserrat, sans-serif; font-weight: 400; font-size: 12px; color: var(--white); letter-spacing: .4px;
  }
</style>
</head>
<body>
<div class="canvas">
  <section class="cover">
    <header class="masthead">
      <div class="brand">
        <div class="brand-mark"></div>
        <div class="brand-name">Pilgrave<br>Law Group</div>
      </div>
      <p class="tagline">Helping Accidents Victim since 1993</p>
    </header>
    <div class="rule-top"></div>

    <div class="photo" role="img" aria-label="Photo: a grandfather and two boys running and flying a kite on a sandy beach by the sea"></div>

    <svg class="base" viewBox="0 0 666 320" preserveAspectRatio="none" aria-hidden="true">
      <defs>
        <linearGradient id="navyFill" x1="0" y1="0" x2="0" y2="1">
          <stop offset="0" stop-color="#173e74"/>
          <stop offset="1" stop-color="#0a2349"/>
        </linearGradient>
      </defs>
      <path d="M0,40 C140,-12 300,50 430,82 C550,110 630,70 666,0 L666,320 L0,320 Z" fill="#3d3f44"/>
      <path d="M0,54 C140,6 300,64 430,96 C550,124 630,88 666,22 L666,320 L0,320 Z" fill="#ffffff"/>
      <path d="M0,66 C140,20 300,76 430,108 C550,136 630,102 666,40 L666,320 L0,320 Z" fill="url(#navyFill)"/>
    </svg>

    <h1 class="headline">
      <span class="light">We’ll help</span><br>
      <span class="light">you get </span><span class="strong">back to</span><br>
      <span class="strong">what you love</span>
    </h1>

    <div class="contact">
      <div class="phone">907 555 0142</div>
      <div class="web">www.pilgravelaw.com</div>
    </div>

    <div class="rule-bottom"></div>
    <p class="address">218 Birch Street • Anchorage, AK 99501</p>
  </section>
</div>
</body>
</html>
```